Home Remodeling company needs a business card design

we need a business card design for home remodeling company in hamilton county, indiana USA. we offers a wide range of construction services including whole house renovations, Design and Build Basements and Kitchen and Bathroom Remodeling . we would like to see designs for both site of business card that use the same color of the company logo and also including all information below :
1- Karim Feltous CEO / General Contractor
2- all company contacts Telephone numbers ( 1-888-DULOM-47 ) ( 317-555-0193) email address ( info@dulomhome.com) website ( www.dulomhome.com ) and social media logos (Facebook- twitter- google plus )
3- company logo
4- licensed . insured . bonded

```html
<!DOCTYPE html>
<html lang="en">
<head>
<meta charset="utf-8">
<title>Dulom Home Remodeling – Business Card</title>
<link rel="stylesheet" href="https://fonts.googleapis.com/css2?family=Cabin:wght@400;600;700&display=swap">
<style>
  :root {
    --page-bg: #9c9c9c;
    --card-light: #ececed;
    --card-dark: #323234;
    --brand-red: #b3262e;
    --ink: #2a2a2c;
    --ink-soft: #3a3a3c;
    --mark-light: #e2e2e2;
    --text-light: #e8e8e8;
    --rule-light: #8d8d8f;
  }
  * { box-sizing: border-box; margin: 0; padding: 0; }
  html, body {
    width: 1105px; height: 1200px; overflow: hidden;
    background: var(--page-bg);
    font-family: "Cabin", "Helvetica Neue", Arial, sans-serif;
  }
  .canvas { position: relative; width: 1105px; height: 1200px; }

  .card {
    position: absolute; left: 182px; width: 746px; height: 427px;
  }
  .card--front { top: 119px; background: var(--card-light); }
  .card--back  { top: 637px; background: var(--card-dark); }

  .edge-stripe {
    position: absolute; top: 0; right: 0; width: 17px; height: 100%;
    background: var(--brand-red);
  }

  .person { position: absolute; left: 58px; top: 44px; }
  .person__name { font-size: 25px; font-weight: 700; color: var(--ink); letter-spacing: 0.2px; }
  .person__role { font-size: 20px; font-weight: 400; color: var(--brand-red); margin-top: 3px; }

  .contacts { position: absolute; left: 58px; top: 165px; list-style: none; }
  .contacts__item {
    display: flex; align-items: center; height: 29px;
    font-size: 19px; color: var(--ink-soft);
  }
  .contacts__icon { width: 18px; height: 18px; margin-right: 15px; fill: var(--ink); flex: none; }

  .brand { position: absolute; left: 58px; top: 299px; display: flex; align-items: flex-start; }
  .brand__square { width: 14px; height: 14px; background: var(--brand-red); margin: 14px 14px 0 0; }
  .brand__name {
    font-size: 58px; line-height: 48px; font-weight: 600; color: var(--ink-soft);
    letter-spacing: 2px;
  }
  .brand__tag {
    display: block; font-size: 18px; line-height: 22px; letter-spacing: 6.4px;
    margin-top: 6px;
  }

  .back-mark {
    position: absolute; left: 308px; top: 126px; width: 131px; height: 131px;
    background: var(--mark-light);
  }
  .credentials {
    position: absolute; left: 0; top: 320px; width: 100%; text-align: center;
    font-size: 21px; color: var(--text-light); letter-spacing: 0.3px;
  }
  .social {
    position: absolute; left: 0; top: 360px; width: 100%;
    display: flex; justify-content: center; align-items: center; gap: 4px;
  }
  .social__rule { width: 55px; height: 1px; background: var(--rule-light); margin: 0 4px; }
  .social__dot { width: 25px; height: 25px; border-radius: 50%; background: var(--text-light); }
</style>
</head>
<body>
<main class="canvas">

  <section class="card card--front" aria-label="Business card front">
    <div class="edge-stripe"></div>

    <div class="person">
      <h1 class="person__name">Karim Feltous</h1>
      <p class="person__role">CEO / General Contractor</p>
    </div>

    <ul class="contacts">
      <li class="contacts__item">
        <svg class="contacts__icon" viewBox="0 0 24 24" aria-hidden="true"><path d="M6.6 10.8a15.2 15.2 0 0 0 6.6 6.6l2.2-2.2c.3-.3.7-.4 1-.2 1.1.4 2.3.6 3.6.6.6 0 1 .4 1 1V20c0 .6-.4 1-1 1A17 17 0 0 1 3 4c0-.6.4-1 1-1h3.5c.6 0 1 .4 1 1 0 1.3.2 2.5.6 3.6.1.3 0 .7-.2 1z"/></svg>
        1-888-DULOM-47
      </li>
      <li class="contacts__item">
        <svg class="contacts__icon" viewBox="0 0 24 24" aria-hidden="true"><path d="M7 1h10a2 2 0 0 1 2 2v18a2 2 0 0 1-2 2H7a2 2 0 0 1-2-2V3a2 2 0 0 1 2-2zm0 3v14h10V4zm5 15.5a1.2 1.2 0 1 0 0 2.4 1.2 1.2 0 0 0 0-2.4z"/></svg>
        317-555-0193
      </li>
      <li class="contacts__item">
        <svg class="contacts__icon" viewBox="0 0 24 24" aria-hidden="true"><path d="M2 5h20v14H2zm2 2v.5l8 5 8-5V7zm0 2.8V17h16V9.8l-8 5z"/></svg>
        info@dulomhome.com
      </li>
      <li class="contacts__item">
        <svg class="contacts__icon" viewBox="0 0 24 24" aria-hidden="true"><path d="M12 2a10 10 0 1 0 0 20 10 10 0 0 0 0-20zm-1 17.9A8 8 0 0 1 4.2 10.4L9 15v1a2 2 0 0 0 2 2zm6.9-2.5A2 2 0 0 0 16 16h-1v-3a1 1 0 0 0-1-1H8v-2h2a1 1 0 0 0 1-1V7h2a2 2 0 0 0 2-2v-.4a8 8 0 0 1 2.9 12.8z"/></svg>
        www.dulomhome.com
      </li>
    </ul>

    <div class="brand">
      <span class="brand__square" aria-hidden="true"></span>
      <p class="brand__name">DULOM<span class="brand__tag">HOME REMODELING</span></p>
    </div>
  </section>

  <section class="card card--back" aria-label="Business card back">
    <div class="back-mark" aria-hidden="true"></div>
    <p class="credentials">LICENSED | INSURED | BONDED</p>
    <div class="social" aria-label="Social media">
      <span class="social__rule"></span>
      <span class="social__dot"></span>
      <span class="social__dot"></span>
      <span class="social__dot"></span>
      <span class="social__rule"></span>
    </div>
  </section>

</main>
</body>
</html>
```